design an extra page for our profile

we are looking for someone to create another page like the attached but with the below changes:
heading changed to (Construction)
icons changed and names to reflect new services i.e
- Residential Building
- Commercial Building
- Landscaping
- Concrete
- Painting

the very bottom of the page is to stay the same with our office info

```html
<!DOCTYPE html>
<html lang="en">
<head>
<meta charset="utf-8">
<title>Construction Services Flyer</title>
<link rel="stylesheet" href="https://fonts.googleapis.com/css2?family=Montserrat:wght@300;400;600;700;800&display=swap">
<style>
  :root {
    --brand-blue: #2e4aa8;
    --ink-blue: #2f3e9c;
    --page: #ffffff;
    --backdrop: #e7e7e7;
    --label: #1d1d1d;
    --photo-light: #f3f3f3;
    --photo-mid: #c9c9c9;
    --photo-dark: #8e8e8e;
  }
  * { margin: 0; padding: 0; box-sizing: border-box; }
  html, body { width: 1200px; height: 1000px; overflow: hidden; }
  body {
    background: var(--backdrop);
    font-family: "Montserrat", sans-serif;
    position: relative;
  }
  .flyer {
    position: absolute;
    left: 280px; top: 30px;
    width: 640px; height: 940px;
    background: var(--page);
    overflow: hidden;
    box-shadow: 0 6px 18px rgba(0,0,0,0.12);
  }
  .city-photo {
    position: absolute; left: 0; top: 0; width: 640px; height: 692px;
    background: linear-gradient(180deg, var(--photo-light) 0%, #e4e4e4 35%, var(--photo-mid) 70%, var(--photo-dark) 100%);
    clip-path: polygon(0 176px, 270px 150px, 640px 150px, 640px 692px, 0 692px);
  }
  .city-photo::after {
    content: ""; position: absolute; inset: 0;
    background: linear-gradient(90deg, rgba(120,120,120,0.35) 0%, rgba(255,255,255,0) 45%, rgba(255,255,255,0.5) 100%);
  }
  .header-shape { position: absolute; left: 0; top: 0; }
  .header-title {
    position: absolute; left: 18px; top: 48px; width: 260px; color: #fff;
  }
  .header-title .main { font-weight: 700; font-size: 24px; letter-spacing: 0.5px; }
  .header-title .rule { height: 1px; background: rgba(255,255,255,0.8); width: 255px; margin: 6px 0 6px; }
  .header-title .sub { font-weight: 300; font-size: 20px; letter-spacing: 0.5px; }
  .brand-name {
    position: absolute; right: 62px; top: 52px;
    display: flex; align-items: center; gap: 10px;
    font-weight: 700; font-size: 34px; color: var(--brand-blue);
  }
  .brand-name .dot { width: 14px; height: 14px; border-radius: 50%; background: var(--brand-blue); }
  .offer {
    position: absolute; left: 0; width: 640px; top: 200px;
    text-align: center; color: var(--ink-blue); text-transform: uppercase;
  }
  .offer .intro { font-size: 16px; font-weight: 400; line-height: 24px; letter-spacing: 0.3px; }
  .offer .discount { font-size: 15px; font-weight: 700; margin-top: 12px; letter-spacing: 0.3px; }
  .service {
    position: absolute; width: 146px; height: 136px;
    border: 1.5px solid var(--brand-blue);
    display: flex; flex-direction: column; align-items: center; justify-content: center; gap: 8px;
  }
  .service svg { width: 70px; height: 60px; fill: none; stroke: var(--brand-blue); stroke-width: 2; stroke-linejoin: round; stroke-linecap: round; }
  .service .name { font-size: 8.5px; font-weight: 800; color: var(--label); text-transform: uppercase; letter-spacing: 0.2px; }
  .residential { left: 56px; top: 336px; }
  .commercial { left: 264px; top: 336px; }
  .landscaping { left: 468px; top: 338px; }
  .concrete { left: 146px; top: 520px; }
  .painting { left: 368px; top: 520px; }
  .hat-photo {
    position: absolute; left: 0; top: 692px; width: 640px; height: 162px;
    background:
      linear-gradient(180deg, rgba(0,0,0,0) 55%, rgba(60,60,60,0.55) 100%),
      linear-gradient(90deg, #9a8b80 0%, #8b7f78 22%, #d4432a 40%, #e24a2e 58%, #b9472f 70%, #7f7b78 85%, #a39a92 100%);
  }
  .footer {
    position: absolute; left: 0; top: 854px; width: 640px; height: 86px;
    background: var(--brand-blue); color: #fff;
  }
  .footer .brand-small {
    position: absolute; left: 22px; top: 30px;
    font-weight: 700; font-size: 17px; color: #fff;
  }
  .footer .office {
    position: absolute; left: 152px; top: 20px; font-size: 12.5px; font-weight: 400;
  }
  .footer .office b { font-weight: 700; }
  .footer .rule { position: absolute; left: 152px; top: 42px; width: 450px; height: 1px; background: rgba(255,255,255,0.7); }
  .footer .web { position: absolute; left: 152px; top: 52px; font-size: 10.5px; font-weight: 600; letter-spacing: 0.2px; }
  .footer .web span { font-weight: 400; }
</style>
</head>
<body>
  <main class="flyer">
    <div class="city-photo" role="img" aria-label="Greyscale photo of a tall round tower under construction with a crane"></div>

    <svg class="header-shape" width="640" height="180" viewBox="0 0 640 180" aria-hidden="true">
      <polygon points="0,0 322,0 262,140 0,164" fill="var(--brand-blue)"/>
    </svg>
    <div class="header-title">
      <div class="main">CONSTRUCTION</div>
      <div class="rule"></div>
      <div class="sub">SERVICES</div>
    </div>
    <div class="brand-name"><span class="dot"></span>Marlow</div>

    <section class="offer">
      <p class="intro">As a new tenants to the building and as a way<br>of introducing ourselves we would like to offer</p>
      <p class="discount">A 10% discount on any &nbsp;of the below services</p>
    </section>

    <div class="service residential">
      <svg viewBox="0 0 70 60"><path d="M10 30 L30 12 L50 30"/><path d="M15 26 V52 H45 V26"/><rect x="26" y="38" width="8" height="14"/><rect x="19" y="30" width="6" height="6"/><rect x="35" y="30" width="6" height="6"/><path d="M40 18 V12 H45 V23"/><path d="M48 52 Q52 42 58 52"/><path d="M4 52 H66"/></svg>
      <span class="name">Residential Building</span>
    </div>
    <div class="service commercial">
      <svg viewBox="0 0 70 60"><rect x="14" y="14" width="14" height="38"/><rect x="32" y="6" width="14" height="46"/><rect x="50" y="24" width="10" height="28"/><path d="M18 20 V48 M24 20 V48 M36 12 V48 M42 12 V48"/><path d="M4 52 H66"/></svg>
      <span class="name">Commercial Building</span>
    </div>
    <div class="service landscaping">
      <svg viewBox="0 0 70 60"><path d="M4 46 Q30 30 66 42"/><path d="M4 54 Q34 40 66 52"/><path d="M20 38 V30 L26 25 L32 30 V36"/><ellipse cx="46" cy="16" rx="6" ry="10"/><path d="M46 26 V38"/><ellipse cx="56" cy="24" rx="4" ry="6"/><path d="M56 30 V38"/></svg>
      <span class="name">Landscaping</span>
    </div>
    <div class="service concrete">
      <svg viewBox="0 0 70 60"><path d="M8 40 V26 L36 18 L40 40 Z"/><path d="M40 24 H54 L62 34 V44 H40 Z"/><path d="M50 24 V34 H62"/><path d="M6 44 H64"/><circle cx="18" cy="48" r="5"/><circle cx="52" cy="48" r="5"/><path d="M14 30 L34 24"/></svg>
      <span class="name">Concrete</span>
    </div>
    <div class="service painting">
      <svg viewBox="0 0 70 60"><rect x="10" y="8" width="40" height="12" rx="2"/><path d="M50 14 H58 V26 H34 V34"/><rect x="30" y="34" width="8" height="20" rx="2"/><path d="M14 20 V30 M22 20 V34 M30 20 V28"/></svg>
      <span class="name">Painting</span>
    </div>

    <div class="hat-photo" role="img" aria-label="Photo of a red safety helmet resting on asphalt with a blurred site behind"></div>

    <footer class="footer">
      <div class="brand-small">Marlow</div>
      <p class="office"><b>HOME OFFICE:</b> 1300 24 8190 . &nbsp;Suite 4.02 , 18 Harbour Lane Kellyville</p>
      <div class="rule"></div>
      <p class="web">WWW.MARLOW-SERVICES.COM.AU &nbsp;<span>SYDNEY &nbsp;| &nbsp;CANBERRA &nbsp;| &nbsp;BRISBANE &nbsp;| &nbsp;MELBOURNE</span></p>
    </footer>
  </main>
</body>
</html>
```